Garlic Farm for Farm Sales/Restaurant sales

Need a professional, but appealing to agriculture world. We are selling 27 kinds of Organic Garlic from a farm in Simla,CO. I have uploaded logo and business information-we are going to need a template, because I will need to use it for four separate people.
-We are trying to appeal to Farm to table restaurants
-As well as growers/farmers

Target Market(s)

Agriculture Sales/Restaurants-Organic

Industry/Entity Type

Agriculture

Contact Information for Business Card

Want it to look more unique then your average kelto stock card- I want it to look amazing

Font styles to use
Sans Serif

Colors
0455a3
ec1f27
fbed22
ffffff

Requirements
Must have
• Just be creative
Nice to have
• Colorful
Should not have
• plain

```html
<!DOCTYPE html>
<html lang="en">
<head>
<meta charset="utf-8">
<title>Ridgeline Gourmet Garlic – Business Card</title>
<link rel="stylesheet" href="https://fonts.googleapis.com/css2?family=Source+Sans+3:wght@400;600&display=swap">
<style>
  :root {
    --backdrop: #e9e6e1;
    --farm-red: #c20e2f;
    --night-blue: #062a5c;
    --garlic-yellow: #ffd800;
    --paper: #ffffff;
    --ink-light: #ffffff;
  }
  html, body {
    margin: 0;
    padding: 0;
    width: 1200px;
    height: 987px;
    overflow: hidden;
    background: var(--backdrop);
    font-family: "Source Sans 3", Arial, sans-serif;
  }
  .canvas {
    position: relative;
    width: 1200px;
    height: 987px;
  }
  .card {
    position: absolute;
    left: 292px;
    width: 616px;
    height: 352px;
    overflow: hidden;
    box-shadow: 0 2px 6px rgba(0,0,0,0.25);
  }
  .card--front { top: 130px; background: var(--night-blue); }
  .card--back  { top: 505px; background: var(--paper); }

  .front__band {
    position: absolute;
    left: 0; top: 0;
    width: 206px; height: 100%;
    background: var(--farm-red);
  }
  .front__garlic {
    position: absolute;
    left: 15px; top: 8px;
    width: 293px; height: 344px;
    border-radius: 48% 48% 44% 44% / 40% 40% 58% 58%;
    background: radial-gradient(ellipse at 50% 60%, #ffe135 0%, var(--garlic-yellow) 65%, #f2c800 100%);
  }
  .front__details {
    position: absolute;
    right: 45px;
    top: 58px;
    text-align: right;
    color: var(--ink-light);
    font-size: 16px;
    line-height: 23px;
  }
  .details__name {
    margin: 0;
    color: var(--garlic-yellow);
    font-weight: 600;
    font-size: 21px;
    line-height: 24px;
  }
  .details__title { margin: 3px 0 10px; }
  .details__address { margin: 0 0 6px; }
  .details__contact { margin: 0; padding: 0; list-style: none; }
  .details__contact li { display: flex; justify-content: flex-end; align-items: center; gap: 6px; }
  .details__contact svg { width: 14px; height: 14px; flex: none; }
  .details__social { display: flex; justify-content: flex-end; gap: 3px; margin-top: 16px; }
  .details__social span {
    width: 26px; height: 26px;
    border: 1.5px solid var(--garlic-yellow);
    border-radius: 50%;
    box-sizing: border-box;
  }

  .back__brand {
    position: absolute;
    left: 0; right: 0;
    top: 150px;
    display: flex;
    justify-content: center;
    align-items: center;
    gap: 14px;
  }
  .brand__dot {
    width: 44px; height: 44px;
    border-radius: 50%;
    background: var(--farm-red);
  }
  .brand__name {
    color: var(--night-blue);
    font-weight: 600;
    font-size: 30px;
  }
</style>
</head>
<body>
<main class="canvas">
  <section class="card card--front">
    <div class="front__band"></div>
    <div class="front__garlic" role="img" aria-label="Illustration of a yellow garlic bulb"></div>
    <div class="front__details">
      <p class="details__name">JORDAN HALE</p>
      <p class="details__title">CEO/FOUNDER</p>
      <p class="details__address">P.O. Box 48<br>Arden, CO&nbsp;&nbsp;80412</p>
      <ul class="details__contact">
        <li>719-555-0148
          <svg viewBox="0 0 16 16" aria-hidden="true"><path fill="#ffd800" d="M3.5 1.5l2.5 0 1 3.5-1.7 1.2a8 8 0 0 0 4.5 4.5l1.2-1.7 3.5 1v2.5c0 1-1 1.5-2 1.5A12 12 0 0 1 2 3.5c0-1 .5-2 1.5-2z"/></svg>
        </li>
        <li>Jo@RidgeGarlic.com
          <svg viewBox="0 0 16 16" aria-hidden="true"><rect x="1" y="3" width="14" height="10" fill="#ffd800"/><path d="M1.5 3.5L8 9l6.5-5.5" fill="none" stroke="#062a5c" stroke-width="1.4"/></svg>
        </li>
        <li>www.RidgeGarlic.com
          <svg viewBox="0 0 16 16" aria-hidden="true"><circle cx="8" cy="8" r="7" fill="#ffd800"/><path d="M1 8h14M8 1c-3 3-3 11 0 14M8 1c3 3 3 11 0 14" fill="none" stroke="#062a5c" stroke-width="1"/></svg>
        </li>
      </ul>
      <div class="details__social" aria-hidden="true"><span></span><span></span><span></span><span></span></div>
    </div>
  </section>

  <section class="card card--back">
    <div class="back__brand">
      <span class="brand__dot"></span>
      <span class="brand__name">Ridgeline Gourmet Garlic</span>
    </div>
  </section>
</main>
</body>
</html>
```